Thornvale Group needs a business card design

We need a new business card design using the logo recently selected in a logo competition on Pixel Bazaar. Our business is a consultancy specializing in aviation and energy and the winning business card design will promote an image of precision and professionalism with creativity.

Please use the logo with the name on the front of the card and use a complementary font. Make the back white with either the light grey or dark grey logo.

Target Market(s)

Senior finance and legal leaders at aviation and energy companies

Industry/Entity Type

Management Consulting

Contact Information for Business Card

Peter Castrell
President
Thornvale Group

www.thornvalegroup.example

(555) 204-6391
pc@thornvalegroup.example

Requirements
Must have
• Professional font that goes well with the logo font

```html
<!DOCTYPE html>
<html lang="en">
<head>
<meta charset="utf-8">
<title>Thornvale Group – Business Card</title>
<link rel="stylesheet" href="https://fonts.googleapis.com/css2?family=Open+Sans:wght@400;600;700&family=Raleway:wght@400&display=swap">
<style>
  :root {
    --page: #e9e9ec;
    --card-top: #f4f4f8;
    --card-bottom: #d9dbe8;
    --brand-blue: #1c5a8c;
    --band-blue: #1a5283;
    --panel-grey: #5d6066;
    --name-ink: #2f3a48;
    --contact-ink: #ffffff;
    --shadow: rgba(30, 35, 50, 0.18);
  }
  html, body {
    margin: 0;
    width: 1200px;
    height: 913px;
    overflow: hidden;
    background: var(--page);
  }
  .canvas {
    position: relative;
    width: 1200px;
    height: 913px;
  }
  .card {
    position: absolute;
    width: 540px;
    height: 309px;
    border-radius: 18px;
    overflow: hidden;
    background: linear-gradient(160deg, var(--card-top), var(--card-bottom));
    box-shadow: 0 10px 28px var(--shadow);
  }
  .card--front { left: 40px; top: 302px; }
  .card--back  { left: 620px; top: 302px; }

  .card__shapes {
    position: absolute;
    inset: 0;
  }

  .wordmark {
    position: absolute;
    font-family: "Raleway", sans-serif;
    font-weight: 400;
    color: var(--brand-blue);
    letter-spacing: 0.08em;
    text-transform: uppercase;
    line-height: 1.15;
    white-space: nowrap;
  }
  .wordmark__line { display: block; }
  .wordmark--front {
    left: 34px;
    top: 128px;
    font-size: 24px;
  }
  .wordmark--front .wordmark__mark {
    display: block;
    width: 32px;
    height: 32px;
    margin-bottom: 12px;
    background: var(--brand-blue);
  }
  .wordmark--back {
    left: 0;
    right: 0;
    top: 100px;
    text-align: center;
    font-size: 44px;
  }

  .identity {
    position: absolute;
    right: 26px;
    top: 22px;
    text-align: right;
    font-family: "Open Sans", sans-serif;
  }
  .identity__name {
    margin: 0;
    font-size: 19px;
    font-weight: 700;
    color: var(--name-ink);
  }
  .identity__title {
    margin: 0;
    font-size: 13px;
    font-weight: 400;
    color: var(--brand-blue);
  }

  .contact {
    position: absolute;
    right: 20px;
    top: 148px;
    margin: 0;
    padding: 0;
    list-style: none;
    font-family: "Open Sans", sans-serif;
    font-size: 12.5px;
    color: var(--contact-ink);
    text-align: right;
  }
  .contact__item {
    display: flex;
    justify-content: flex-end;
    align-items: center;
    gap: 8px;
    line-height: 21px;
  }
  .contact__icon {
    width: 11px;
    height: 11px;
    flex: none;
  }
</style>
</head>
<body>
<main class="canvas">

  <section class="card card--front" aria-label="Business card front">
    <svg class="card__shapes" viewBox="0 0 540 309" aria-hidden="true">
      <polygon points="300,112 540,62 540,309 220,309" fill="var(--band-blue)"/>
      <polygon points="330,122 540,80 540,309 262,309" fill="var(--panel-grey)"/>
    </svg>

    <div class="wordmark wordmark--front">
      <span class="wordmark__mark"></span>
      <span class="wordmark__line">Thornvale</span>
      <span class="wordmark__line">Group</span>
    </div>

    <div class="identity">
      <p class="identity__name">Peter Castrell</p>
      <p class="identity__title">President</p>
    </div>

    <ul class="contact">
      <li class="contact__item">(555) 204-6391
        <svg class="contact__icon" viewBox="0 0 12 12" aria-hidden="true"><path d="M2.5 1l2 2.2-1 1.3a6 6 0 0 0 4 4l1.3-1 2.2 2-1.2 1.5C5 10.8 1.2 7 1 2.2z" fill="#fff"/></svg>
      </li>
      <li class="contact__item">pc@thornvalegroup.example
        <svg class="contact__icon" viewBox="0 0 12 12" aria-hidden="true"><rect x="1" y="2.5" width="10" height="7" fill="none" stroke="#fff" stroke-width="1.2"/><path d="M1 2.5l5 4 5-4" fill="none" stroke="#fff" stroke-width="1.2"/></svg>
      </li>
      <li class="contact__item">www.thornvalegroup.example
        <svg class="contact__icon" viewBox="0 0 12 12" aria-hidden="true"><circle cx="6" cy="6" r="4.8" fill="none" stroke="#fff" stroke-width="1.1"/><path d="M1.2 6h9.6M6 1.2c-2.4 2.6-2.4 7 0 9.6M6 1.2c2.4 2.6 2.4 7 0 9.6" fill="none" stroke="#fff" stroke-width="0.9"/></svg>
      </li>
    </ul>
  </section>

  <section class="card card--back" aria-label="Business card back">
    <div class="wordmark wordmark--back">
      <span class="wordmark__line">Thornvale</span>
      <span class="wordmark__line">Group</span>
    </div>
  </section>

</main>
</body>
</html>
```